Brochure for a civil enineering company in A4 format

I need a brochure design for our company TIRO Engineering S.r.l.. We are an engineering consultant company. Our main clients are from the infrastructure industry (geotechnical and underground sectors mainly).
We are looking for a 2 pages (4 faces) fold out design with a glued pocket where we can put individual data sheets.
I need A4 format pages.

Target Market(s)

We are an engineering consultant company. Our main clients are from the infrastructure industry (geotechnical and underground sectors mainly).

Industry/Entity Type

Civil Engineer

Font styles to use
Sans Serif

Requirements
Must have
• Overall: 2 pages in A4 format
Essential style. Bright and modern appearance.
Glued pocket
Logo integrated in a picture on the pocket where I would like to insert a slogan (… tiro engineering … reliable solutions …)
Attached are selected images which the designer can use and edit at their own discretion.
Some advice in the following (anyway designers are free to provide their solutions):
Outer sheets:
Front page with name, logo. It could be nice to have the “m” of the logo integrated in a pictures, also a modified picture (I mean modify one of the attached pictures) so to create a general image and do not tie the cover to a specific job.
Back page: offices address and contact email address. Nice to have one space for a slogan.
Inner sheet: text that I upload in the file “inside-sheets”, possibly with pictures on each sheet. In the right faces insert the glued pocket. On this pages insert the section OUR EXPERIENCE ….with a space for a picture of our team.
Nice to have
• Clean and essential design.
Pictures choosing from the atteched ones. Pictures could be modified in a very light manner to make them a general idea of the work ( I mean geotechnical world) without to be immediately linked to a specific site.
Should not have
• excessive frills

```html
<!DOCTYPE html>
<html lang="it">
<head>
<meta charset="utf-8">
<title>TIRO Engineering – Brochure</title>
<link href="https://fonts.googleapis.com/css2?family=Montserrat:wght@300;400;500;600;700&display=swap" rel="stylesheet">
<style>
:root{
  --stage:#8a8a8a;
  --paper:#ffffff;
  --paper-soft:#f1f1f1;
  --ink:#1b1b1b;
  --ink-soft:#4a4a4a;
  --rule:#2a2a2a;
  --band-dark:#1a1a1a;
  --on-dark:#e6e6e6;
}
*{margin:0;padding:0;box-sizing:border-box}
html,body{width:888px;height:1200px;overflow:hidden}
body{background:var(--stage);font-family:"Montserrat",sans-serif;color:var(--ink);position:relative}
.spread{position:absolute;left:103px;width:682px;height:482px;background:var(--paper)}
.spread--outer{top:80px}
.spread--inner{top:640px;height:482px}
.panel{position:absolute;top:0;width:341px;height:100%;overflow:hidden}
.panel--left{left:0;background:linear-gradient(160deg,#e2e2e2 0%,#f4f4f4 45%,#ffffff 100%)}
.panel--right{left:341px;background:linear-gradient(200deg,#ececec 0%,#f8f8f8 50%,#ffffff 100%)}
.abs{position:absolute}

.section-title{position:absolute;font-size:12px;font-weight:600;letter-spacing:.2px;color:var(--ink);white-space:nowrap}
.section-title .light{font-weight:300}
.section-rule{position:absolute;height:1px;background:var(--rule)}

/* offices */
.office{position:absolute;left:35px;font-size:7px;line-height:9.6px;font-weight:500;color:var(--ink)}
.office .row{display:flex;align-items:center;gap:5px}
.office .ico{width:7px;height:7px;flex:none}
.office .pad{padding-left:12px}
.office .spacer{width:7px;flex:none}

.wordmark{position:absolute;font-family:"Montserrat",sans-serif;font-weight:600;color:var(--ink);letter-spacing:1px;line-height:1}
.tagline{position:absolute;font-size:4.3px;letter-spacing:1px;color:var(--ink-soft);white-space:nowrap;font-weight:500}

.photo-frame{position:absolute;left:225px;top:103px;width:457px;height:277px;background:var(--paper)}
.photo{position:absolute}
.photo--crane{left:230px;top:106px;width:277px;height:270px;background:linear-gradient(180deg,#2a7fd0 0%,#4fa0e0 45%,#a5492f 70%,#6e6a66 100%)}
.photo--tunnel{left:511px;top:106px;width:166px;height:148px;background:radial-gradient(circle at 60% 65%,#c7b9d6 0%,#4f4f8c 40%,#24244d 100%)}
.photo--portals{left:511px;top:258px;width:166px;height:117px;background:linear-gradient(180deg,#b9c9d8 0%,#8e8574 40%,#5c554b 100%)}

.cover-title{position:absolute;left:391px;top:392px;width:240px;text-align:center;font-size:14.6px;font-weight:600;letter-spacing:.3px;white-space:nowrap}
.cover-band{position:absolute;left:391px;top:412px;width:240px;height:20px;background:var(--band-dark);color:#fff;font-size:14.6px;font-weight:500;letter-spacing:.6px;text-align:center;line-height:20px;white-space:nowrap}
.cover-web{position:absolute;left:391px;top:444px;width:240px;text-align:center;font-size:6.6px;letter-spacing:1px;color:var(--ink-soft)}
.cover-web b{font-weight:600;color:var(--ink)}

/* inner */
.company-band{position:absolute;left:0;top:0;width:341px;height:202px}
.company-band .photo-fill{position:absolute;inset:0;background:linear-gradient(160deg,#263026 0%,#1c211d 40%,#3b3d3b 75%,#2c2e2e 100%)}
.company-band .shade{position:absolute;inset:0;background:rgba(20,20,20,.55)}
.on-dark{color:#fff}
.on-dark-rule{background:#d8d8d8}

.copy{position:absolute;left:35px;width:270px;text-align:justify;font-size:5.3px;line-height:7.9px;font-weight:400}
.copy p{margin-bottom:4.4px}
.copy--dark{color:var(--on-dark)}
.copy--light{color:var(--ink-soft)}
.copy .strong{font-weight:600;color:var(--ink)}

.service-item{position:absolute;left:32px;width:273px;display:flex;align-items:flex-start;gap:6px}
.service-item .icon{width:17px;height:17px;flex:none}
.service-item .bar{width:1px;height:22px;background:var(--rule);flex:none}
.service-item .text{font-size:5.3px;line-height:7.9px;color:var(--ink-soft);text-align:justify}

.copy--right{left:34px;width:271px}
.founders-tab{position:absolute;left:32px;top:103px;width:149px;height:13px;background:var(--band-dark);color:#fff;font-size:8px;font-weight:500;line-height:13px;padding-left:10px;clip-path:polygon(0 0,92% 0,100% 100%,0 100%);letter-spacing:.3px}
.founders-rule{position:absolute;left:175px;top:115px;width:130px;height:1px;background:var(--rule)}
.bio{position:absolute;left:34px;width:271px;font-size:4.6px;line-height:6.9px;color:var(--ink-soft);text-align:justify}

.photo--shaft{left:34px;top:375px;width:98px;height:87px;background:linear-gradient(180deg,#8e8a80 0%,#b7a98e 50%,#6d6a63 100%)}
.photo--site{left:138px;top:375px;width:167px;height:87px;background:linear-gradient(160deg,#4f6b3f 0%,#8a8d86 45%,#c47a4a 70%,#5b7a45 100%)}
.bottom-band{position:absolute;left:0;bottom:0;width:682px;height:3px;background:var(--band-dark)}
</style>
</head>
<body>

<!-- Outer spread: back cover + front cover -->
<section class="spread spread--outer">
  <div class="panel panel--left">
    <h2 class="section-title" style="left:35px;top:297px"><span class="light">OUR </span>OFFICES</h2>
    <div class="section-rule" style="left:35px;top:316px;width:150px"></div>

    <div class="office" style="top:323px">
      <div class="pad">Milano</div>
      <div class="row"><svg class="ico" viewBox="0 0 10 10"><path d="M5 1a3 3 0 0 1 3 3c0 2.2-3 5.5-3 5.5S2 6.2 2 4a3 3 0 0 1 3-3z" fill="none" stroke="#1b1b1b" stroke-width="1"/><circle cx="5" cy="4" r="1" fill="#1b1b1b"/></svg><span>Via Lentini, 14</span></div>
      <div class="row"><span class="spacer"></span><span>20121 Milano - IT</span></div>
      <div class="row" style="margin-top:3px"><svg class="ico" viewBox="0 0 10 10"><circle cx="5" cy="5" r="4.2" fill="none" stroke="#1b1b1b" stroke-width=".9"/><path d="M3.5 3.2l1 1-.5.6c.4.8 1 1.4 1.7 1.7l.6-.5 1 1-.7.8C4.8 7.6 2.7 5.5 2.8 3.9z" fill="#1b1b1b"/></svg><span>+39 02 5550 1234</span></div>
      <div class="row"><svg class="ico" viewBox="0 0 10 10"><rect x="1" y="2.5" width="8" height="5.5" fill="none" stroke="#1b1b1b" stroke-width=".9"/><path d="M1 2.5l4 3 4-3" fill="none" stroke="#1b1b1b" stroke-width=".9"/></svg><span>info@tiroengineering.example</span></div>
    </div>

    <div class="office" style="top:384px">
      <div class="pad">Rovere TN</div>
      <div class="row"><svg class="ico" viewBox="0 0 10 10"><path d="M5 1a3 3 0 0 1 3 3c0 2.2-3 5.5-3 5.5S2 6.2 2 4a3 3 0 0 1 3-3z" fill="none" stroke="#1b1b1b" stroke-width="1"/><circle cx="5" cy="4" r="1" fill="#1b1b1b"/></svg><span>Via dei Tigli, 9</span></div>
      <div class="row"><span class="spacer"></span><span>38062 Rovere TN - IT</span></div>
      <div class="row" style="margin-top:3px"><svg class="ico" viewBox="0 0 10 10"><circle cx="5" cy="5" r="4.2" fill="none" stroke="#1b1b1b" stroke-width=".9"/><path d="M3.5 3.2l1 1-.5.6c.4.8 1 1.4 1.7 1.7l.6-.5 1 1-.7.8C4.8 7.6 2.7 5.5 2.8 3.9z" fill="#1b1b1b"/></svg><span>+39 02 5550 1234</span></div>
      <div class="row"><svg class="ico" viewBox="0 0 10 10"><rect x="1" y="2.5" width="8" height="5.5" fill="none" stroke="#1b1b1b" stroke-width=".9"/><path d="M1 2.5l4 3 4-3" fill="none" stroke="#1b1b1b" stroke-width=".9"/></svg><span>info@tiroengineering.example</span></div>
    </div>

    <div class="office" style="top:444px">
      <div class="row"><svg class="ico" viewBox="0 0 10 10"><circle cx="5" cy="5" r="4" fill="none" stroke="#1b1b1b" stroke-width=".8"/><ellipse cx="5" cy="5" rx="1.8" ry="4" fill="none" stroke="#1b1b1b" stroke-width=".7"/><path d="M1 5h8" stroke="#1b1b1b" stroke-width=".7"/></svg><span>www.tiroengineering.example</span></div>
    </div>

    <div class="wordmark" style="left:230px;top:426px;font-size:20px">TIRO</div>
    <div class="tagline" style="left:230px;top:448px;font-size:2.6px;letter-spacing:.6px">TIRO ENGINEERING . RELIABLE SOLUTIONS</div>
  </div>

  <div class="panel panel--right"></div>

  <div class="wordmark" style="left:452px;top:34px;font-size:36px;letter-spacing:3px">TIRO</div>
  <div class="tagline" style="left:447px;top:68px">TIRO ENGINEERING . RELIABLE SOLUTIONS</div>

  <div class="photo-frame"></div>
  <div class="photo photo--crane" role="img" aria-label="Crawler crane lifting a tunnel boring machine shield on a construction site"></div>
  <div class="photo photo--tunnel" role="img" aria-label="Twin tunnel excavation lit from inside"></div>
  <div class="photo photo--portals" role="img" aria-label="Tunnel portals cut into a hillside with site machinery"></div>

  <div class="cover-title">LOREM IPSUM DOLOR SIT AMET</div>
  <div class="cover-band">CONSECTETUR ADIPISCING</div>
  <div class="cover-web">www.<b>TiroEngineering</b>.example</div>
</section>

<!-- Inner spread: company and services + expertise -->
<section class="spread spread--inner">
  <div class="panel panel--left">
    <div class="company-band">
      <div class="photo-fill" role="img" aria-label="Aerial view of a wooded valley with an infrastructure construction site"></div>
      <div class="shade"></div>
      <h2 class="section-title on-dark" style="left:35px;top:26px"><span class="light">OUR </span>COMPANY</h2>
      <div class="section-rule on-dark-rule" style="left:35px;top:48px;width:270px"></div>
      <div class="copy copy--dark" style="top:56px">
        <p>TIRO Engineering S.r.l. offre servizi di consulenza tecnica, contrattuale e strategica ai principali attori nei settori della geologia, della geotecnica e dell'idraulica. Lavoriamo per ridurre il rischio e l'incertezza, cercando con flessibilità la soluzione migliore per la redditività del progetto.</p>
        <p>TIRO Engineering S.r.l. è una società indipendente nata nel 2020 dall'incontro di un gruppo di professionisti che uniscono oltre trent'anni di esperienza come progettisti e consulenti nelle grandi opere di ingegneria civile, in ruoli di direzione tecnica e come liberi professionisti.</p>
        <p>TIRO Engineering S.r.l. unisce l'esperienza dei fondatori all'entusiasmo di chi inizia un nuovo percorso, con un obiettivo chiaro: progettare infrastrutture sicure, sostenibili ed economiche.</p>
        <p>Each of our projects is a long term commitment: we deliver safe, reliable, sustainable and innovative solutions. This is our distinctive character.</p>
      </div>
    </div>

    <h2 class="section-title" style="left:35px;top:216px"><span class="light">OUR </span>SERVICES</h2>
    <div class="section-rule" style="left:35px;top:235px;width:270px"></div>
    <div class="copy copy--light" style="top:242px">
      <p>Progettazione e consulenza specialistica nel campo della geologia, della geotecnica, delle opere in sotterraneo e dell'ingegneria idraulica.</p>
      <p>Aiutiamo i clienti a risolvere problemi progettuali, contrattuali e costruttivi lungo tutta la vita del progetto, portando la nostra esperienza nelle loro organizzazioni, migliorando la qualità dei servizi di ingegneria e proponendo idee e soluzioni nuove.</p>
      <p>Offriamo assistenza lungo l'intero iter procedurale, dalle indagini preliminari e dagli studi di fattibilità fino alla progettazione costruttiva e all'assistenza in cantiere.</p>
      <p class="strong" style="margin-top:6px">L'esperienza maturata nelle discipline della geologia, della geotecnica, del sottosuolo e dell'idraulica ci permette di massimizzare la nostra efficacia quando serve:</p>
    </div>

    <div class="service-item" style="top:373px">
      <svg class="icon" viewBox="0 0 20 20"><circle cx="10" cy="10" r="5" fill="none" stroke="#1b1b1b" stroke-width="1.1"/><circle cx="10" cy="10" r="2" fill="none" stroke="#1b1b1b" stroke-width="1.1"/><path d="M10 2v3M10 15v3M2 10h3M15 10h3M4.3 4.3l2.1 2.1M13.6 13.6l2.1 2.1M4.3 15.7l2.1-2.1M13.6 6.4l2.1-2.1" stroke="#1b1b1b" stroke-width="1.1"/></svg>
      <span class="bar"></span>
      <span class="text">affrontare emergenze anche su progetti in fase avanzata, focalizzando subito le criticità e garantendo il risultato atteso in qualità, tempi e costi;</span>
    </div>
    <div class="service-item" style="top:403px">
      <svg class="icon" viewBox="0 0 20 20"><path d="M10 3l6 3.5v7L10 17l-6-3.5v-7z M4 6.5l6 3.5 6-3.5M10 10v7" fill="none" stroke="#1b1b1b" stroke-width="1.1"/></svg>
      <span class="bar"></span>
      <span class="text">fornire una second opinion di alto valore tecnico e amministrativo in caso di criticità progettuali, costruttive o dispute legali;</span>
    </div>
    <div class="service-item" style="top:428px">
      <svg class="icon" viewBox="0 0 20 20"><path d="M5 9a5 5 0 0 1 10 0z M3.5 9h13" fill="none" stroke="#1b1b1b" stroke-width="1.1"/><path d="M4 18c0-3 2.7-5 6-5s6 2 6 5" fill="none" stroke="#1b1b1b" stroke-width="1.1"/></svg>
      <span class="bar"></span>
      <span class="text">analizzare in tempi brevi progetti di terzi, individuandone le criticità e verificandone la cantierabilità e la validità economica;</span>
    </div>
    <div class="service-item" style="top:452px">
      <svg class="icon" viewBox="0 0 20 20"><rect x="2" y="10" width="10" height="4" fill="none" stroke="#1b1b1b" stroke-width="1.1"/><circle cx="4.5" cy="16" r="1.5" fill="none" stroke="#1b1b1b" stroke-width="1"/><circle cx="9.5" cy="16" r="1.5" fill="none" stroke="#1b1b1b" stroke-width="1"/><path d="M12 11l4-6 2 4" fill="none" stroke="#1b1b1b" stroke-width="1.1"/></svg>
      <span class="bar"></span>
      <span class="text">ottimizzare progetti redatti da terzi, migliorandone il contenuto e massimizzando l'efficacia economica degli investimenti.</span>
    </div>
  </div>

  <div class="panel panel--right">
    <h2 class="section-title" style="left:34px;top:26px"><span class="light">OUR </span>EXPERTISE AND EXPERIENCE</h2>
    <div class="section-rule" style="left:34px;top:48px;width:271px"></div>
    <div class="copy copy--light copy--right" style="top:56px">
      <p>La società nasce dall'associazione di un gruppo di professionisti con solide competenze e affidabilità, maturate in oltre trent'anni come progettisti e consulenti nelle grandi opere civili; geologia, geotecnica e opere in sotterraneo sono il cuore del loro lavoro.</p>
    </div>

    <div class="founders-tab">I SOCI FONDATORI SONO:</div>
    <div class="founders-rule"></div>

    <p class="bio" style="top:125px">Marco. Già direttore tecnico e socio di Studio Valdo Srl fino al 2018, ha firmato tutti i progetti di opere in sotterraneo e gran parte di quelli geotecnici della società. Dal 2019 è direttore tecnico di Geotecna. Vanta oltre 150 gallerie naturali e numerosi progetti di strutture geotecniche, sistemazioni idrogeologiche e protezione ambientale. Negli ultimi dieci anni ha guidato l'assistenza tecnica in corso d'opera per lavori oltre 440 milioni di euro e la progettazione esecutiva per opere oltre 1.400 milioni. Ha svolto verifiche e validazioni in Italia e all'estero per progetti di valore complessivo superiore a 3.400 milioni.</p>
    <p class="bio" style="top:198px">Paolo. Trent'anni di esperienza professionale. Ha lavorato a oltre 150 gallerie naturali per una lunghezza complessiva di più di 360 km, con numerosi progetti e attività di assistenza su strutture, sistemazioni idrogeologiche e opere di protezione ambientale. Negli ultimi dieci anni ha seguito l'assistenza tecnica in corso d'opera per lavori oltre 440 milioni di euro e la progettazione esecutiva per opere oltre 1.400 milioni, oltre a verifiche e validazioni in Italia e all'estero.</p>
    <p class="bio" style="top:257px">Giulia. Trent'anni di esperienza professionale. Ha lavorato a oltre 150 gallerie naturali per una lunghezza complessiva di più di 360 km, con numerosi progetti e attività di assistenza su strutture, sistemazioni idrogeologiche e opere di protezione ambientale. Negli ultimi dieci anni ha seguito l'assistenza tecnica in corso d'opera per lavori oltre 440 milioni di euro e la progettazione esecutiva per opere oltre 1.400 milioni, oltre a verifiche e validazioni in Italia e all'estero.</p>
    <p class="bio" style="top:316px">Chiara. Trent'anni di esperienza professionale. Ha lavorato a oltre 150 gallerie naturali per una lunghezza complessiva di più di 360 km, con numerosi progetti e attività di assistenza su strutture, sistemazioni idrogeologiche e opere di protezione ambientale. Negli ultimi dieci anni ha seguito l'assistenza tecnica in corso d'opera per lavori oltre 440 milioni di euro e la progettazione esecutiva per opere oltre 1.400 milioni, oltre a verifiche e validazioni in Italia e all'estero.</p>

    <div class="photo photo--shaft" role="img" aria-label="Excavated shaft with tunnel entrance and steel bracing"></div>
    <div class="photo photo--site" role="img" aria-label="Aerial view of a tunnel construction yard with sheds and machinery"></div>
  </div>

  <div class="bottom-band"></div>
</section>

</body>
</html>
```